Launching a new real estate agency in Monaco

Hello, I am opening a new real estate agency in Monaco. For the purpose of my activity, in order to be known quickly among a fierce competition I need an advertising campaign that will be broadcast in local magazines, newspapers, paper board, etc.

You will find example of pictures of Monaco on which I have the rights and my logo. You can always pick other images that I can buy if the price is reasonable for a commercial use (<200 $)

Please respect the color code.

I wish you good luck and look forward to give you my feedbacks

Reason: Only few projects posted were respecting the brief and of quality. Hoping to receive more in coming days

Target Market(s)

International high-end clientele of all ages, all genders.

Industry/Entity Type

Real Estate Agent

Font styles to use
Serif

Requirements
Must have
• 1/ My logo
• 2/ This message "Un nouveau regard sur l'immobilier" means in English a fresh look at real estate or new eyes on real-estate.
• 3/ My address: 14 rue des Ormeaux, Galerie Bellerive Nord, 98 000 Monaco
• 4/ Phone number: +377.93.48.25.07
• 5/ Website: www.corvano-immo.com.
• 6/ Format: Files should be easily adjustable but I'd like a vertical display to fit easily in Magazines, Poster and billboard. So please work in high resolution !
Nice to have
• Please think about your design in accordance with the message I want to display.
Should not have
• A simple poster with a picture of Monaco that does not take into consideration the message of the advertisement, "Un nouveau regard sur l'immobilier" which means in english, new eyes on real-estate or a new look at real-estate, or new vision at real-estate.

```html
<!DOCTYPE html>
<html lang="fr">
<head>
<meta charset="utf-8">
<title>Corvano Immo – Un nouveau regard sur l'immobilier</title>
<link href="https://fonts.googleapis.com/css2?family=Lato:wght@400;700&display=swap" rel="stylesheet">
<style>
  :root {
    --bg: #000000;
    --rose-gold: #d9967f;
    --text-light: #d8d8d8;
    --rule: #7a7a7a;
    --frame-hot: #ff9a3c;
    --frame-deep: #b4420f;
  }
  html, body {
    margin: 0;
    padding: 0;
    background: var(--bg);
    overflow: hidden;
  }
  .poster {
    position: relative;
    width: 849px;
    height: 1200px;
    background: var(--bg);
    font-family: 'Lato', sans-serif;
    color: var(--text-light);
    overflow: hidden;
  }
  .brand {
    position: absolute;
    top: 118px;
    left: 0;
    width: 100%;
    display: flex;
    justify-content: center;
    align-items: center;
    gap: 18px;
  }
  .brand-mark {
    width: 22px;
    height: 22px;
    background: var(--rose-gold);
  }
  .brand-name {
    font-size: 46px;
    font-weight: 700;
    letter-spacing: 6px;
    color: var(--rose-gold);
    line-height: 1;
  }
  .window {
    position: absolute;
    left: 170px;
    top: 228px;
    width: 560px;
    height: 600px;
  }
  .tagline {
    position: absolute;
    top: 926px;
    left: 0;
    width: 100%;
    text-align: center;
    font-size: 33px;
    font-weight: 400;
    color: var(--text-light);
    margin: 0;
  }
  .contact {
    position: absolute;
    top: 1030px;
    left: 54px;
    width: 740px;
    border-top: 1.5px solid var(--rule);
    padding-top: 10px;
    text-align: center;
    font-size: 21.5px;
    line-height: 33px;
    color: var(--text-light);
  }
  .contact p { margin: 0; }
  .contact .sep { margin: 0 16px; }
</style>
</head>
<body>
<main class="poster">
  <header class="brand">
    <span class="brand-mark" aria-hidden="true"></span>
    <span class="brand-name">CORVANO IMMO</span>
  </header>

  <svg class="window" viewBox="0 0 560 600" xmlns="http://www.w3.org/2000/svg">
    <defs>
      <linearGradient id="frameGlow" x1="0" y1="0" x2="1" y2="0">
        <stop offset="0" stop-color="#3a1204"/>
        <stop offset="0.25" stop-color="#7a2a08"/>
        <stop offset="0.8" stop-color="var(--frame-hot)"/>
        <stop offset="1" stop-color="var(--frame-deep)"/>
      </linearGradient>
      <linearGradient id="viewTones" x1="0" y1="0" x2="0" y2="1">
        <stop offset="0" stop-color="#ffb25a"/>
        <stop offset="0.15" stop-color="#c9708a"/>
        <stop offset="0.35" stop-color="#9b6aa6"/>
        <stop offset="0.6" stop-color="#5b3a55"/>
        <stop offset="0.85" stop-color="#7a4a2a"/>
        <stop offset="1" stop-color="#2a1a18"/>
      </linearGradient>
    </defs>
    <rect class="window-frame" x="10" y="4" width="540" height="592" rx="120" fill="url(#frameGlow)"/>
    <rect class="window-view" x="42" y="16" width="416" height="568" rx="80"
          fill="url(#viewTones)" role="img"
          aria-label="Aerial photograph of Monaco at sunset, seen through an airplane window"/>
  </svg>

  <h1 class="tagline">Un nouveau regard sur l'immobilier</h1>

  <footer class="contact">
    <p>14 rue des Ormeaux, Galerie Bellerive Nord, 98 000 Monaco</p>
    <p>Phone: +377.93.48.25.07<span class="sep">I</span>Website: www.corvano-immo.com</p>
  </footer>
</main>
</body>
</html>
```